Agricultural equipment sales and financing flyer

I need an agricultural sales and financing flyer that can double as a contact poster that you would put on a bulletin board with contact information and phone number in the form of tear off stubs ast the bottom and contact info on the main poster. For efficiencies sake, I want this poster/flyer to be dimensioned to fit on 8.5x11 inch sheet of paper.

I've included a logo for our company for you to use in the creation of this poster. When making the poster, follow the color scheme on the logo (orange, black and a little bit of red) this is our brand coloring.

-I do not want a poster that looks like it was made with scrap art images in microsoft word
-I've included a very rough sketch of what I envisioned in a poster, my designing clearly sucks in hindsight, but follow what the format looks like (ei logo near the top, target market below it, then services offered, then why our services are better and at the bottom, removable cut away tickets of phone contact information.
-I want the ability to change the worded content so that if our address or phone number or any details change, I can simply open this file, for example, in Microsoft Publisher and just input new details and reprint.

Target Market(s)

farmers

Industry/Entity Type

Agriculture

Font styles to use
Other font styles liked:
• Just use a professional looking, simple font

Colors
f78f20
ec1f27
000000
606060
ffffff
f5f5f5
eaeaea

Requirements
Must have
• -8.5x11 inch dimensioned poster
• -use company colors as sampled in logo attached
• -removable contact information tabs at bottom of poster that people can remove from poster
Nice to have
• -although i have listed general colors used below. Only use colors a sampled from the logo.
Should not have
• -a dark background, i don't want to pay a fortune in ink costs at the printer

```html
<!DOCTYPE html>
<html lang="en">
<head>
<meta charset="utf-8">
<title>Agri-Equipment Leasing Flyer</title>
<link href="https://fonts.googleapis.com/css2?family=Oswald:wght@400;500;600;700&family=Roboto+Condensed:wght@400;500;700&display=swap" rel="stylesheet">
<style>
  :root {
    --orange: #f78f20;
    --orange-deep: #e9771a;
    --red: #ec1f27;
    --black: #000000;
    --charcoal: #2a2a2a;
    --grey: #606060;
    --white: #ffffff;
    --paper: #f5f5f5;
    --rule: #eaeaea;
  }
  * { box-sizing: border-box; margin: 0; padding: 0; }
  html, body { width: 960px; height: 1200px; overflow: hidden; background: var(--paper); }
  .flyer {
    position: relative; width: 960px; height: 1200px; overflow: hidden;
    background: linear-gradient(180deg, var(--orange) 0%, var(--orange-deep) 45%, var(--orange) 100%);
    font-family: "Roboto Condensed", Arial, sans-serif;
    color: var(--black); text-align: center;
  }
  .brand {
    position: absolute; top: 22px; left: 0; width: 100%;
    display: flex; flex-direction: column; align-items: center; gap: 6px;
  }
  .brand-mark { width: 116px; height: 116px; border-radius: 50%; background: var(--black); }
  .brand-name {
    font-family: "Oswald", Arial, sans-serif; font-weight: 600; font-size: 20px;
    color: var(--black); letter-spacing: 0.5px; line-height: 1;
  }
  .headline {
    position: absolute; top: 190px; left: 0; width: 100%;
    font-family: "Oswald", Arial, sans-serif; font-weight: 600; font-size: 56px;
    color: var(--white); letter-spacing: 1px; line-height: 1;
  }
  .pitch {
    position: absolute; left: 120px; width: 720px;
    font-family: "Oswald", Arial, sans-serif; font-weight: 500; font-size: 26px;
    line-height: 1.05; color: var(--black); text-transform: uppercase;
    padding-bottom: 8px; border-bottom: 3px dotted var(--black);
  }
  .pitch.leasing { top: 262px; }
  .pitch.maintenance { top: 342px; border-bottom: none; }
  .benefits-band {
    position: absolute; top: 412px; left: 148px; width: 664px; height: 64px;
    background: var(--charcoal); color: var(--orange);
    font-family: "Oswald", Arial, sans-serif; font-weight: 500; font-size: 36px;
    line-height: 64px; text-transform: uppercase;
  }
  .benefits-list {
    position: absolute; top: 492px; left: 166px; width: 628px; list-style: none;
    color: var(--white); font-size: 26px; line-height: 1.2;
  }
  .benefits-list li { padding: 3px 0 5px; border-bottom: 3px dotted var(--black); }
  .benefits-list li:last-child { border-bottom: none; }
  .field-photo {
    position: absolute; top: 640px; left: 0; width: 960px; height: 320px;
    background: linear-gradient(180deg, rgba(247,143,32,0) 0%, #d9772a 30%, #a0582a 62%, #5a3a1f 100%);
  }
  .stubs-rule { position: absolute; top: 960px; left: 0; width: 960px; height: 10px; background: var(--red); }
  .stubs {
    position: absolute; top: 970px; left: 0; width: 960px; height: 230px;
    background: var(--white); display: flex;
  }
  .stub {
    flex: 0 0 120px; width: 120px; height: 230px; overflow: hidden;
    border-right: 2px dashed var(--rule);
    display: flex; align-items: center; justify-content: center;
  }
  .stub:last-child { border-right: none; }
  .stub-text {
    writing-mode: vertical-rl; white-space: nowrap; text-align: left;
    display: flex; flex-direction: column-reverse; gap: 3px;
    max-height: 216px;
  }
  .stub-name { font-family: "Oswald", Arial, sans-serif; font-weight: 600; font-size: 13px; line-height: 1.1; color: var(--black); }
  .stub-line { font-size: 10px; line-height: 1.1; color: var(--grey); }
  .stub-phone { font-family: "Oswald", Arial, sans-serif; font-weight: 600; font-size: 21px; line-height: 1.1; color: var(--red); }
</style>
</head>
<body>
  <main class="flyer">
    <header class="brand">
      <div class="brand-mark"></div>
      <div class="brand-name">Ridgeline Production Services Ltd.</div>
    </header>

    <h1 class="headline">"AGRI-EQUIPMENT LEASING"</h1>

    <p class="pitch leasing">Flexible leasing and financing options that<br>will turn heads keep your coast down.</p>
    <p class="pitch maintenance">24 hour maintenance services for your machines.<br>Let no breakdown leave you in dust.</p>

    <div class="benefits-band">Benefits offered throgh us</div>
    <ul class="benefits-list">
      <li>Alberta based solutions that keep you high and dry.</li>
      <li>Commercial wholesale rates on leasing and financing</li>
      <li>Long term relationships, personal relationship : ME</li>
      <li>Prompt service delivered Alberta local in part by veterans</li>
    </ul>

    <div class="field-photo" role="img" aria-label="Photo of a row of tractors in a harvested field at orange sunset"></div>

    <div class="stubs-rule"></div>
    <section class="stubs" aria-label="Tear-off contact stubs">
      <div class="stub"><div class="stub-text"><span class="stub-name">Ridgeline Production Services Ltd.</span><span class="stub-line">Field Services &amp; Maintenance</span><span class="stub-phone">780-555-0142</span></div></div>
      <div class="stub"><div class="stub-text"><span class="stub-name">Ridgeline Production Services Ltd.</span><span class="stub-line">Field Services &amp; Maintenance</span><span class="stub-phone">780-555-0142</span></div></div>
      <div class="stub"><div class="stub-text"><span class="stub-name">Ridgeline Production Services Ltd.</span><span class="stub-line">Field Services &amp; Maintenance</span><span class="stub-phone">780-555-0142</span></div></div>
      <div class="stub"><div class="stub-text"><span class="stub-name">Ridgeline Production Services Ltd.</span><span class="stub-line">Field Services &amp; Maintenance</span><span class="stub-phone">780-555-0142</span></div></div>
      <div class="stub"><div class="stub-text"><span class="stub-name">Ridgeline Production Services Ltd.</span><span class="stub-line">Field Services &amp; Maintenance</span><span class="stub-phone">780-555-0142</span></div></div>
      <div class="stub"><div class="stub-text"><span class="stub-name">Ridgeline Production Services Ltd.</span><span class="stub-line">Field Services &amp; Maintenance</span><span class="stub-phone">780-555-0142</span></div></div>
      <div class="stub"><div class="stub-text"><span class="stub-name">Ridgeline Production Services Ltd.</span><span class="stub-line">Field Services &amp; Maintenance</span><span class="stub-phone">780-555-0142</span></div></div>
      <div class="stub"><div class="stub-text"><span class="stub-name">Ridgeline Production Services Ltd.</span><span class="stub-line">Field Services &amp; Maintenance</span><span class="stub-phone">780-555-0142</span></div></div>
    </section>
  </main>
</body>
</html>
```